Spring Detox sale graphics for social media

You MUST read the Brief in the WORD document and follow the instructions there. I want to create 10 social media graphics (new Instagram size 4:5 (1080 x 1350 pixels) focusing on our Mother’s Day Spring Detox Sale graphics, using any of the pics attached. Use the attached pics, NO RANDOM STOCK PHOTOGRAPHY. For the color scheme of the graphics, they should all be complementary to the product colors or feel like Spring time.

Target Market(s)

primarily women

Requirements
Must have
• the photos and text attached

```html
<!DOCTYPE html>
<html lang="en">
<head>
<meta charset="utf-8">
<title>Mother's Day Spring Detox Sale – Social Set</title>
<link rel="stylesheet" href="https://fonts.googleapis.com/css2?family=Poppins:wght@800&family=Parisienne&display=swap">
<style>
  :root {
    --sky: #7fc3ee;
    --white: #ffffff;
    --coral: #f9958a;
    --coral-script: #ee4b47;
    --blue-soft: #c6e0f3;
    --blue-pale: #e8f2fa;
    --green: #4f9a7d;
    --ink: #111418;
  }
  * { margin: 0; padding: 0; box-sizing: border-box; }
  html, body { width: 1069px; height: 1200px; overflow: hidden; }
  body { background: var(--sky); position: relative; }

  .post {
    position: absolute;
    width: 382px;
    height: 478px;
    background: var(--white);
    overflow: hidden;
  }
  .post--mother-model { left: 121px; top: 93px; }
  .post--mother-bottles { left: 566px; top: 93px; }
  .post--all-supplements { left: 121px; top: 630px; }
  .post--spring-reset { left: 566px; top: 630px; }

  .post__shapes { position: absolute; inset: 0; width: 100%; height: 100%; }

  .headline, .script {
    position: absolute;
    line-height: 1;
    white-space: nowrap;
    z-index: 2;
  }
  .headline {
    font-family: "Poppins", "Arial Black", sans-serif;
    font-weight: 800;
    color: var(--ink);
    letter-spacing: -0.5px;
  }
  .script {
    font-family: "Parisienne", cursive;
    color: var(--coral-script);
  }

  .discount-band {
    position: absolute;
    left: 329px; top: 132px;
    width: 53px; height: 237px;
    background: var(--green);
    display: flex; align-items: center; justify-content: center;
    z-index: 2;
  }
  .discount-band span {
    font-family: "Poppins", "Arial Black", sans-serif;
    font-weight: 800;
    font-size: 44px;
    color: var(--white);
    transform: rotate(90deg);
    white-space: nowrap;
    line-height: 1;
  }

  .photo {
    position: absolute;
    border-radius: 6px;
    z-index: 1;
  }
  .photo--model {
    left: 70px; top: 164px; width: 180px; height: 300px;
    background: linear-gradient(180deg, #f6f4f2 0%, #ece8e6 55%, #e6ecf2 100%);
  }
  .photo--bottles {
    left: 39px; top: 261px; width: 292px; height: 174px;
    background: linear-gradient(90deg, #eceef6 0%, #eef4f0 35%, #f6ecec 65%, #f4eaf2 100%);
  }
</style>
</head>
<body>

  <section class="post post--mother-model">
    <svg class="post__shapes" viewBox="0 0 382 478" preserveAspectRatio="none" aria-hidden="true">
      <path d="M0,16 C70,50 86,140 82,230 C78,320 60,400 130,478 L0,478 Z" fill="var(--blue-soft)"/>
      <path d="M0,42 C50,70 62,140 58,220 C54,310 30,400 120,478 L0,478 Z" fill="var(--coral)"/>
      <path d="M180,478 C220,420 290,410 330,420 C360,430 372,455 382,478 Z" fill="var(--blue-soft)"/>
    </svg>
    <div class="headline" style="left:30px;top:16px;font-size:42px;">MOTHER’S DAY</div>
    <div class="script" style="left:77px;top:48px;font-size:42px;">Spring</div>
    <div class="headline" style="left:170px;top:92px;font-size:36px;">DETOX</div>
    <div class="script" style="left:258px;top:122px;font-size:33px;">Sale</div>
    <div class="photo photo--model" role="img" aria-label="Photo of a smiling woman in a white top standing behind a row of supplement bottles"></div>
    <div class="discount-band"><span>25% OFF</span></div>
  </section>

  <section class="post post--mother-bottles">
    <svg class="post__shapes" viewBox="0 0 382 478" preserveAspectRatio="none" aria-hidden="true">
      <path d="M0,16 C70,50 86,140 82,230 C78,320 70,400 140,478 L0,478 Z" fill="var(--blue-soft)"/>
      <path d="M0,42 C50,70 62,140 58,220 C54,310 40,410 120,478 L0,478 Z" fill="var(--coral)"/>
      <path d="M150,478 C200,420 290,400 340,420 C365,432 376,452 382,468 L382,478 Z" fill="var(--blue-soft)"/>
    </svg>
    <div class="script" style="left:202px;top:28px;font-size:39px;">25% Off</div>
    <div class="headline" style="left:32px;top:94px;font-size:43px;">MOTHER’S DAY</div>
    <div class="headline" style="left:146px;top:145px;font-size:60px;">SPRING</div>
    <div class="script" style="left:99px;top:206px;font-size:31px;">Detox Sale</div>
    <div class="photo photo--bottles" role="img" aria-label="Photo of four white supplement bottles with blue, green, red and pink labels"></div>
  </section>

  <section class="post post--all-supplements">
    <svg class="post__shapes" viewBox="0 0 382 478" preserveAspectRatio="none" aria-hidden="true">
      <path d="M0,0 L230,0 C250,60 250,150 210,210 C170,260 90,270 0,260 Z" fill="var(--blue-pale)"/>
      <path d="M382,0 L382,478 L0,478 L0,390 C60,360 180,340 260,330 C320,320 300,260 270,200 C240,130 300,60 382,0 Z" fill="var(--blue-pale)" opacity="0.7"/>
      <path d="M0,420 C60,380 160,390 230,395 C300,400 340,380 382,360 L382,478 L0,478 Z" fill="var(--blue-soft)"/>
      <path d="M382,35 C320,70 310,150 330,230 C350,320 340,410 250,478 L382,478 Z" fill="var(--coral)"/>
    </svg>
    <div class="script" style="left:126px;top:48px;font-size:39px;">25% Off</div>
    <div class="headline" style="left:40px;top:112px;font-size:63px;">ALL</div>
    <div class="headline" style="left:123px;top:184px;font-size:29px;">SUPPLEMENTS</div>
    <div class="headline" style="left:40px;top:230px;font-size:60px;">SPRING</div>
    <div class="script" style="left:160px;top:300px;font-size:32px;">Detox Sale</div>
  </section>

  <section class="post post--spring-reset">
    <svg class="post__shapes" viewBox="0 0 382 478" preserveAspectRatio="none" aria-hidden="true">
      <path d="M0,0 L225,0 C210,70 160,115 80,115 C40,115 15,108 0,100 Z" fill="var(--coral)"/>
      <path d="M235,0 C250,60 330,110 382,150 L382,0 Z" fill="var(--blue-pale)"/>
      <path d="M260,0 C275,50 340,90 382,115 L382,0 Z" fill="var(--coral)"/>
      <path d="M382,240 C330,300 250,330 200,390 C170,430 160,460 160,478 L382,478 Z" fill="var(--blue-soft)"/>
      <path d="M382,360 C330,350 270,380 225,478 L382,478 Z" fill="var(--coral)"/>
      <path d="M0,398 C70,405 120,440 135,478 L0,478 Z" fill="var(--blue-soft)"/>
    </svg>
    <div class="script" style="left:12px;top:18px;font-size:39px;">25% Off</div>
    <div class="headline" style="left:14px;top:140px;font-size:44px;">SPRING DETOX</div>
    <div class="script" style="left:164px;top:192px;font-size:33px;">Sale</div>
    <div class="headline" style="left:28px;top:228px;font-size:49px;">SPRING RESET</div>
    <div class="script" style="left:97px;top:296px;font-size:31px;">Summer Ready</div>
  </section>

</body>
</html>
```